Bry7Legal Letterhead

Need a new letterhead for my law firm.
IDENTIFYING INFORMATION BELOW:
Anselmo R Quintara III
Attorney at Law
Address: 2847 Larkspur Blvd, Ste 300, Dallas, TX 75204
Phone: 877-482-6017
Fax: 469-738-1452
Email: bry@bry7legal.example
Website: www.bry7legal.example

Colors
0054AA
0677BA
7BADD7
CADEEF
E8F1F8

Requirements
Must have
• Logo needs to be on the letterhead, along with identifying information which is included in the project description.

```html
<!DOCTYPE html>
<html lang="en">
<head>
<meta charset="utf-8">
<title>Bry7Legal Letterhead</title>
<link rel="stylesheet" href="https://fonts.googleapis.com/css2?family=Montserrat:wght@300;800&family=Oswald:wght@500&family=Roboto:wght@400;500&family=Source+Sans+3:wght@400;600&display=swap">
<style>
  :root {
    --backdrop: #ababab;
    --paper-light: #ffffff;
    --paper-dark: #d2d2d2;
    --ink: #111111;
    --body-ink: #4a4a4a;
    --accent: #0a8fd0;
    --rule: #b8b8b8;
    --watermark: rgba(150, 150, 150, 0.22);
  }
  * { margin: 0; padding: 0; box-sizing: border-box; }
  html, body { width: 1039px; height: 1200px; overflow: hidden; background: var(--backdrop); }
  .letterhead {
    position: absolute; left: 114px; top: 30px; width: 810px; height: 1140px;
    background: linear-gradient(135deg, var(--paper-light) 0%, #efefef 45%, var(--paper-dark) 100%);
    overflow: hidden;
  }
  .brand { position: absolute; left: 62px; top: 56px; width: 260px; text-align: center; }
  .brand-name {
    font-family: "Montserrat", sans-serif; font-weight: 800; font-size: 34px;
    letter-spacing: 1px; color: var(--ink); line-height: 1; text-transform: uppercase;
  }
  .brand-tagline {
    margin-top: 8px; font-family: "Montserrat", sans-serif; font-weight: 300;
    font-size: 15px; letter-spacing: 2px; color: var(--ink); text-transform: uppercase;
  }
  .contact {
    position: absolute; right: 602px; top: 170px; width: 200px; text-align: right;
    font-family: "Roboto", sans-serif; font-size: 12px; color: var(--ink); line-height: 15px;
  }
  .contact-name {
    font-family: "Oswald", sans-serif; font-weight: 500; font-size: 18px;
    color: var(--accent); text-transform: uppercase; line-height: 22px;
  }
  .contact-role { margin-bottom: 9px; }
  .contact-label { font-weight: 500; color: var(--accent); margin-top: 9px; }
  .divider { position: absolute; left: 230px; top: 169px; width: 1px; height: 834px; background: var(--rule); }
  .letter {
    position: absolute; left: 261px; top: 168px; width: 478px;
    font-family: "Source Sans 3", sans-serif; font-size: 10.6px; line-height: 16.4px;
    color: var(--body-ink); text-align: justify;
  }
  .letter p { margin-bottom: 16.4px; }
  .letter .greeting { font-weight: 600; }
  .letter .closing { margin-top: 32px; }
  .signature-area { display: block; width: 90px; height: 30px; margin-top: 12px; background: linear-gradient(90deg, rgba(30,40,60,0.18), rgba(30,40,60,0)); }
  .watermark {
    position: absolute; left: 0; right: 0; top: 1026px; text-align: center;
    font-family: "Montserrat", sans-serif; font-weight: 800; font-size: 92px;
    letter-spacing: 2px; color: var(--watermark); text-transform: uppercase; line-height: 1; white-space: nowrap;
  }
</style>
</head>
<body>
<main class="letterhead">
  <header class="brand">
    <div class="brand-name">Bry7Legal</div>
    <div class="brand-tagline">Legal Made Clear</div>
  </header>

  <aside class="contact">
    <div class="contact-name">Anselmo R Quintara III</div>
    <div class="contact-role">Attorney at Law</div>
    <div class="contact-label">Address</div>
    <div>2847 Larkspur Blvd<br>Ste 300, Dallas, TX 75204</div>
    <div class="contact-label">Phone</div>
    <div>877-482-6017</div>
    <div class="contact-label">Fax</div>
    <div>469-738-1452</div>
    <div class="contact-label">Email</div>
    <div>bry@bry7legal.example</div>
    <div class="contact-label">Web</div>
    <div>www.bry7legal.example</div>
  </aside>

  <div class="divider"></div>

  <section class="letter">
    <p class="greeting">Dear Mr. Smith,</p>
    <p>Lorem ipsum dolor sit amet, consectetur adipiscing elit. Donec orci purus, luctus vitae dignissim eu, iaculis sed purus. Vivamus faucibus, ipsum nec aliquet viverra, leo mauris condimentum ligula, sit amet sagittis enim ligula quis arcu. Nam egestas tortor id nisi porttitor mattis. In tortor ante, ultricies in suscipit a, tempus non massa. Vivamus et auctor mi. Fusce vel massa nulla. Phasellus nec eros mauris, et scelerisque orci.</p>
    <p>Donec malesuada orci vitae nulla accumsan porta a id massa. Quisque accumsan iaculis magna sit amet fringilla. Maecenas consequat, magna eget tincidunt semper, odio nibh rutrum mi, id feugiat ante nisi eu risus. Vestibulum nunc orci, rhoncus a placerat in, ultricies in mi. Cras mattis varius eros, vel fringilla nisi suscipit eget. Quisque scelerisque sagittis nulla at porttitor.</p>
    <p>Sed id augue vitae urna euismod commodo aliquet a quam. Pellentesque arcu velit, cursus et malesuada ut, consequat et diam. Nullam erat sem, rhoncus id ullamcorper vitae, rhoncus et arcu. In ultricies ultricies nulla, ut rutrum nisi iaculis at. Donec eu magna a metus ornare faucibus. Fusce aliquet faucibus ultricies. Morbi semper, est id tincidunt gravida, sem arcu adipiscing lacus, ac bibendum nulla leo eu purus. Quisque nec diam sed risus consectetur a ccumsan quis quis nibh. Vestibulum id purus lorem.</p>
    <p>It is a long established fact that a reader will be distracted by the readable content of a page when looking at its layout. The point of using Lorem Ipsum is that it has a more-or-less normal distribution of letters, as opposed to using 'Content here, content here', making it look like readable English. Many desktop publishing packages</p>
    <p>ut rutrum nisi iaculis at. Donec eu magna a metus ornare faucibus. Fusce aliquet faucibus ultricies. Morbi semper, est id tincidunt gravida, sem arcu adipiscing lacus, ac bibendum nulla leo eu purus. Quisque nec diam sed risus consectetur a ccumsan quis quis nibh. Vestibulum id purus lorem.</p>
    <p>ultricies ultricies nulla, ut rutrum nisi iaculis at. Donec eu magna a metus ornare faucibus. Fusce aliquet faucibus ultricies. Morbi semper, est id tincidunt gravida, sem arcu adipiscing lacus, ac bibendum nulla leo eu purus. Quisque nec diam sed risus consectetur a ccumsan quis quis nibh. Vestibulum id purus lorem.</p>
    <p>It is a long established fact that a reader will be distracted by the readable content of a page when looking at its layout. ut rutrum nisi iaculis at.</p>
    <p>The point of using Lorem Ipsum is that it has a more-or-less normal distribution of letters, as opposed to using 'Content here, content here', making it look like readable English. Many desktop publishing packages</p>
    <p>ut rutrum nisi iaculis at. Donec eu magna a metus ornare faucibus. Fusce aliquet faucibus ultricies. Morbi semper, est id tincidunt gravida,</p>
    <p class="closing">Sincerely,</p>
    <span class="signature-area" role="img" aria-label="Handwritten signature of the attorney"></span>
  </section>

  <div class="watermark" aria-hidden="true">Bry7Legal</div>
</main>
</body>
</html>
```